Modern Business Card

Modern professional business card with more than just logo and demographic info. Something memorable.

We are a trendy/modern chiropractic group with an emphasis on neurology, hence the minimalist-type brain logo. We want to convey that modern and technical aspect with professionalism and the elite nature of our practice environment.

```html
<!DOCTYPE html>
<html lang="en">
<head>
<meta charset="utf-8">
<title>Keystone Spine Care – Business Card</title>
<link rel="stylesheet" href="https://fonts.googleapis.com/css2?family=Marcellus&family=Arimo:wght@400&display=swap">
<style>
  :root {
    --page-bg: #e9e6e3;
    --card-black: #000000;
    --brand-blue: #3f7fc4;
    --text-white: #ffffff;
    --text-soft: #f2f2f2;
    --frost-light: #ffffff;
    --frost-shade: #e4e4e6;
  }
  html, body {
    margin: 0;
    padding: 0;
    width: 1200px;
    height: 900px;
    overflow: hidden;
    background: var(--page-bg);
  }
  .business-card {
    position: absolute;
    left: 160px;
    top: 175px;
    width: 880px;
    height: 550px;
    background: var(--card-black);
    overflow: hidden;
    box-shadow: 0 12px 30px rgba(0,0,0,0.18);
  }
  .accent-band {
    position: absolute;
    top: 0;
    right: 0;
    width: 212px;
    height: 100%;
    background: var(--brand-blue);
  }
  .feature-square {
    position: absolute;
    left: 520px;
    top: 115px;
    width: 320px;
    height: 320px;
    border-radius: 28px;
    background: linear-gradient(135deg, var(--frost-light) 0%, var(--frost-shade) 55%, var(--frost-light) 100%);
  }
  .brand {
    position: absolute;
    left: 52px;
    top: 52px;
    display: flex;
    align-items: center;
    gap: 26px;
  }
  .brand-square {
    width: 52px;
    height: 52px;
    background: var(--brand-blue);
  }
  .brand-name {
    font-family: "Marcellus", serif;
    color: var(--text-white);
    line-height: 1;
    margin: 0;
    font-weight: 400;
  }
  .brand-name .line-main {
    display: block;
    font-size: 56px;
    letter-spacing: 1px;
  }
  .brand-name .line-sub {
    display: block;
    font-size: 29px;
    letter-spacing: 1.5px;
    margin-top: 4px;
  }
  .contact-block {
    position: absolute;
    left: 52px;
    top: 240px;
    font-family: "Arimo", sans-serif;
    color: var(--text-soft);
  }
  .person-name {
    font-family: "Marcellus", serif;
    color: var(--brand-blue);
    font-size: 31px;
    letter-spacing: 1px;
    margin: 0;
    font-weight: 400;
  }
  .person-role {
    font-size: 25px;
    margin: 4px 0 0 0;
  }
  .address {
    font-size: 25px;
    line-height: 33px;
    margin: 20px 0 0 0;
    font-style: normal;
  }
  .contact-list {
    list-style: none;
    padding: 0;
    margin: 20px 0 0 0;
    font-size: 25px;
    line-height: 33px;
  }
  .contact-list li {
    display: flex;
    align-items: center;
    gap: 10px;
  }
  .contact-icon {
    width: 24px;
    height: 24px;
    flex: none;
  }
</style>
</head>
<body>
  <div class="business-card">
    <div class="accent-band"></div>
    <div class="feature-square" role="img" aria-label="Large frosted brand decoration area"></div>

    <div class="brand">
      <div class="brand-square"></div>
      <h1 class="brand-name">
        <span class="line-main">KEYSTONE</span>
        <span class="line-sub">SPINE CARE</span>
      </h1>
    </div>

    <div class="contact-block">
      <h2 class="person-name">DANIEL HARPER</h2>
      <p class="person-role">Managing Director</p>
      <address class="address">58 Meridian Avenue<br>Northfield, 20417</address>
      <ul class="contact-list">
        <li>
          <svg class="contact-icon" viewBox="0 0 24 24" aria-hidden="true">
            <rect x="1.5" y="1.5" width="21" height="21" rx="3" fill="none" stroke="#3f7fc4" stroke-width="2"/>
            <path d="M8 6c-1 0-2 1-2 2 0 5 5 10 10 10 1 0 2-1 2-2l-3-2-1.5 1.5c-2-1-3.5-2.5-4.5-4.5L10.5 9 8 6z" fill="#3f7fc4"/>
          </svg>
          <span>020-555 0187</span>
        </li>
        <li>
          <svg class="contact-icon" viewBox="0 0 24 24" aria-hidden="true">
            <rect x="1" y="5" width="22" height="15" fill="#3f7fc4"/>
            <path d="M1 5l11 8 11-8" fill="none" stroke="#000" stroke-width="1.6"/>
          </svg>
          <span>hello@keystonespine.example</span>
        </li>
        <li>
          <svg class="contact-icon" viewBox="0 0 24 24" aria-hidden="true">
            <circle cx="12" cy="12" r="10.5" fill="#3f7fc4"/>
            <g fill="none" stroke="#000" stroke-width="1.3">
              <ellipse cx="12" cy="12" rx="4.5" ry="10.5"/>
              <line x1="1.5" y1="12" x2="22.5" y2="12"/>
              <line x1="12" y1="1.5" x2="12" y2="22.5"/>
              <path d="M3.5 7h17M3.5 17h17"/>
            </g>
          </svg>
          <span>www.keystonespine.example</span>
        </li>
      </ul>
    </div>
  </div>
</body>
</html>
```